WE ARE BRIGHT SPARROW, building a full website with ecommerce

requirements:
CODED FOR SITEQUILL
ONLINE STORE FUNCTION WITH E-COMMERCE USING TRADEBLOOM
PAGEWAVE AND PICTOLANE LINKS

I need a website design for my organization, WE ARE BRIGHT SPARROW, a global empowerment movement elevating woman, and the world. The site's home page should reflect our mission, to empower women. It should have a strong, empowering feel, with minimalistic design.
Please see www.lunavelto.com and http://www.corvenhal.co/ for an inspiration on layout and feel.

**PLEASE SEE ATTACHMENT "LOGO MOCK UP" FOR LOGO. THIS IS NOT THE FINAL VECTOR FILE, BUT THIS LOOKS THE SAME AS THE FINAL LOGO.

HOME PAGE:
The first section of the home page should include a background image with our logo center.

You should include the following links to pages at the top right of the page:
MISSION
MANTRA
ARMOR
MEET BS (I would like "bs" to be our logo)
pagewave and pictolane links

As you scroll down the page, you should see the following sections, which correlate to the links to pages as written above. **SEE ATTACHED SKETCH "HOMEPAGE LAYOUT IDEA" FOR REFERENCE**

WHO WE ARE (correlates to the link Mission)

OUR MANTRA (correlates to the link Mantra)

OUR ARMOR (correlates to the link The Shirt)
(This is where we will sell a shirt (and other apparel) and need the e-commerce function)

MEET BRIGHT SPARROWS (correlates to the link Meet BS)

SHOW OFF YOUR SUPER POWERS (correlates to the pagewave and pictolane)

FEATURED BRIGHT SPARROW (no link on top right of page)

On the homepage, for each of the above sections, as you scroll down there should be an image, either in the background or framed, next to the title (WHO WE ARE, for example), as well as one sentence of small text explaining the title. The title (WHO WE ARE) and the one sentence should link to a page (ie WHO WE ARE + the one sentence links to the MISSION page). ** SEE ATTACHED SKETCH "HOMEPAGE SECTION IDEAS" FOR REFERENCE**

**PLEASE SEE ATTACHMENT "WEBSITE TITLE IDEAS" FOR A STARTING PLACE OF THE LOOK. These don't have to be exact, but they give you an idea of what I'm looking for.

**FONTS TYPOLD EXTRA BOLD AND TYPOLD BOOK 500 (WHICH SHOULD BE BOLDED MANUALLY) ARE ATTACHED**

Target Market(s)

Women, mainly in US

Industry/Entity Type

Social

Coding

Coded - Design and coding required

Number of Pages Required

5+ page

Font styles to use
Other font styles liked:
• Typol Extra Bold

Requirements
Must have
• CODED FOR SITEQUILL
• ONLINE STORE FUNCTION WITH E-COMMERCE USING TRADEBLOOM
• PAGEWAVE AND PICTOLANE LINKS
• Typold Extra Bold and Typold Book 500, attached
• please see description for all requirements
Nice to have
• please see description for all ideas
Should not have

```html
<!DOCTYPE html>
<html lang="en">
<head>
<meta charset="utf-8">
<title>We Are Bright Sparrow</title>
<link href="https://fonts.googleapis.com/css2?family=Montserrat:wght@400;500;600;700;800&family=Open+Sans:wght@400;600&display=swap" rel="stylesheet">
<style>
:root{
  --teal:#3fdcc5;
  --teal-dark:#2fc9b2;
  --ink:#1d1d1d;
  --grey:#6b6b6b;
  --white:#ffffff;
  --price:#e8334a;
  --star:#f2b400;
  --line:#dcdcdc;
  --pw:#3b5998;
  --pl:#3f729b;
}
*{margin:0;padding:0;box-sizing:border-box}
html,body{width:1200px;height:3636px;overflow:hidden}
body{position:relative;background:var(--white);font-family:"Open Sans",Arial,sans-serif;color:var(--ink)}
a{text-decoration:none;color:inherit}
.abs{position:absolute}
.content{z-index:6}

/* header */
.topline{left:0;top:0;width:1200px;height:5px;background:var(--teal)}
.site-header{left:0;top:5px;width:1200px;height:116px;background:var(--white);z-index:20}
.brand{left:97px;top:30px;display:flex;align-items:center;gap:14px}
.brand-square{width:40px;height:40px;border:4px solid var(--ink)}
.brand-name{font-family:"Montserrat",sans-serif;font-weight:800;font-size:19px;line-height:20px;color:var(--ink)}
.main-nav{left:540px;top:57px;font-family:"Montserrat",sans-serif;font-size:15px;font-weight:500;letter-spacing:.5px}
.main-nav a,.foot-nav a{position:absolute;white-space:nowrap;color:var(--ink);display:flex;align-items:center;gap:6px}
.nav-square{display:inline-block;width:12px;height:12px;border:2px solid var(--ink)}
.header-social{left:965px;top:50px;display:flex;gap:12px;align-items:center}
.social-link{display:flex;align-items:center;gap:6px;font-family:"Montserrat",sans-serif;font-weight:500;font-size:12px;color:var(--ink);white-space:nowrap}
.social-dot{width:22px;height:22px;border-radius:50%;background:var(--pw)}
.social-dot.alt{background:var(--pl)}

/* photo fills */
.photo{position:absolute;inset:0}
.band{position:absolute;left:0;width:1200px;overflow:hidden}

/* hero */
.hero{top:121px;height:620px;clip-path:polygon(0 0,100% 0,100% 519px,50% 606px,0 519px)}
.hero .photo{background:linear-gradient(100deg,#c9d3dc 0%,#e4e6e8 35%,#d9c9b6 60%,#4a4a50 80%,#9fb0c2 100%)}
.hero-edge{top:121px;height:640px;background:var(--teal);clip-path:polygon(0 519px,50% 606px,100% 519px,100% 535px,50% 622px,0 535px)}
.hero-mark{left:550px;top:255px;width:100px;height:100px;border:8px solid var(--white)}
.hero-title{left:0;width:1200px;top:395px;text-align:center;color:var(--white);font-family:"Montserrat",sans-serif;font-weight:700;font-size:30px;letter-spacing:1px}
.hero-sub{left:0;width:1200px;top:438px;text-align:center;color:var(--white);font-family:"Montserrat",sans-serif;font-weight:400;font-size:27px}
.signup{display:flex;height:44px}
.signup .field{width:456px;background:var(--white);border:1px solid #e2e2e2;font-size:12px;color:#666;padding:0 24px;display:flex;align-items:center}
.signup .go{width:133px;background:var(--teal);color:var(--white);font-family:"Montserrat",sans-serif;font-weight:700;font-size:13px;display:flex;align-items:center;justify-content:center}
.hero-form{left:305px;top:504px}

/* intro */
.badge-square{width:56px;height:56px;border:6px solid var(--teal);background:var(--white)}
.intro-mark{left:572px;top:708px;z-index:5}
.intro-title{left:0;width:1200px;top:818px;text-align:center;font-family:"Montserrat",sans-serif;font-weight:700;font-size:26px;letter-spacing:.5px}
.intro-sub{left:0;width:1200px;top:864px;text-align:center;font-family:"Montserrat",sans-serif;font-size:21px;letter-spacing:.5px;color:#333}
.fly-box{left:533px;top:916px;width:131px;height:68px;border:2px solid #bbb;display:flex;align-items:center;justify-content:center;gap:8px;font-family:"Montserrat",sans-serif;color:var(--ink);line-height:18px}
.fly-box .sq{width:18px;height:18px;border:3px solid var(--ink)}
.fly-box small{display:block;font-size:12px;font-weight:500}
.fly-box b{display:block;font-size:22px;font-weight:800}

/* sections */
.who{top:982px;height:400px;clip-path:polygon(0 0,50% 85px,100% 0,100% 100%,0 100%)}
.who .photo{background:linear-gradient(90deg,#6f6f6f 0%,#8b8b8b 45%,#5b5350 75%,#3a3330 100%)}
.mantra{top:1300px;height:410px;background:var(--teal);clip-path:polygon(0 40px,100% 40px,100% 325px,50% 410px,0 325px)}
.mantra .photo{background:radial-gradient(ellipse 360px 240px at 260px 210px,rgba(255,255,255,.28),rgba(255,255,255,0))}
.meet{top:1620px;height:400px}
.meet .photo{background:linear-gradient(180deg,#2d2622 0%,#7a5838 40%,#c59a6a 62%,#5a4536 100%)}
.armor{top:1940px;height:500px;background:linear-gradient(120deg,#f4f4f4,#ffffff 50%,#ececec);clip-path:polygon(0 60px,50% 0,100% 60px,100% 410px,50% 495px,0 410px)}
.show{top:2340px;height:400px}
.show .photo{background:linear-gradient(90deg,#b9b2ab 0%,#a29990 50%,#8a8f95 75%,#d6c6b0 100%)}
.featured{top:2642px;height:461px;background:var(--teal);clip-path:polygon(0 85px,50% 0,100% 85px,100% 376px,50% 461px,0 376px)}

.title-lockup{display:flex;align-items:center;gap:12px;font-family:"Montserrat",sans-serif;line-height:.95}
.lockup-square{width:60px;height:60px;border:7px solid currentColor;flex:none}
.lockup-text b{display:block;font-weight:800}
.lockup-text span{display:block;font-weight:400}
.on-dark{color:var(--white)}
.on-light{color:var(--ink)}
.divider{width:2px;background:rgba(255,255,255,.45)}
.divider.dark{background:#c9c9c9}
.copy{font-size:13px;line-height:27px}
.copy.light{color:var(--white)}

/* armor */
.product-photo{left:97px;top:2080px;width:200px;height:250px;background:radial-gradient(ellipse 90px 110px at 50% 52%,#1f5fc4,#2a64c0 60%,#eef0f3 100%)}
.product-name{left:349px;top:2095px;font-family:"Montserrat",sans-serif;font-weight:400;font-size:23px;letter-spacing:.5px;color:#333}
.product-desc{left:349px;top:2133px;width:420px;font-size:13px;line-height:24px;color:#888}
.price{left:349px;top:2190px;font-family:"Montserrat",sans-serif;font-size:26px;color:var(--price)}
.stars{left:455px;top:2196px;font-size:15px;color:var(--star);letter-spacing:1px}
.spec{left:349px;font-size:13px;color:#555}
.cart{left:349px;top:2288px;width:126px;height:33px;background:var(--teal);color:var(--white);font-family:"Montserrat",sans-serif;font-weight:700;font-size:11px;display:flex;align-items:center;justify-content:center;letter-spacing:.5px}

/* show off */
.social-big{font-family:"Montserrat",sans-serif;font-weight:700;font-size:20px;color:var(--white);display:flex;align-items:center;gap:10px}
.social-big i{width:16px;height:16px;border-radius:50%;border:3px solid var(--white)}

/* featured */
.member{width:194px;height:194px}
.member-photo{position:absolute;left:28px;top:28px;width:138px;height:138px;transform:rotate(45deg);border:5px solid var(--white);border-radius:14px;box-shadow:0 3px 10px rgba(0,0,0,.2)}
.member-name{width:300px;text-align:center;font-family:"Montserrat",sans-serif;font-size:15px;letter-spacing:.5px;color:#333}
.member-role{width:300px;text-align:center;font-size:12px;color:#4a7f78}

/* join */
.join-mark{left:572px;top:3135px;z-index:5}
.join-title{left:0;width:1200px;top:3235px;text-align:center;font-family:"Montserrat",sans-serif;font-weight:700;font-size:30px;letter-spacing:1px}
.join-copy{left:0;width:1200px;top:3285px;text-align:center;font-size:13px;line-height:29px;color:#777}
.join-form{left:305px;top:3357px}
.foot-social{left:478px;top:3452px;display:flex;gap:22px}
.foot-social .social-dot{width:40px;height:40px}
.foot-nav{left:390px;top:3514px;font-family:"Montserrat",sans-serif;font-size:14px;letter-spacing:.5px}
.copyright{left:0;width:1200px;top:3562px;text-align:center;font-size:11px;color:#888}
</style>
</head>
<body>

<div class="abs topline"></div>
<header class="abs site-header">
  <a class="abs brand" href="#"><span class="brand-square"></span><span class="brand-name">WE ARE<br>BRIGHT<br>SPARROW</span></a>
  <nav class="abs main-nav">
    <a href="#mission" style="left:0;top:0">MISSION</a>
    <a href="#mantra" style="left:112px;top:0">MANTRA</a>
    <a href="#meet" style="left:222px;top:0">MEET BS <span class="nav-square"></span></a>
    <a href="#shirt" style="left:334px;top:0">THE SHIRT</a>
  </nav>
  <div class="abs header-social">
    <a class="social-link" href="#"><span class="social-dot"></span>PAGEWAVE</a>
    <a class="social-link" href="#"><span class="social-dot alt"></span>PICTOLANE</a>
  </div>
</header>

<!-- hero -->
<div class="band hero-edge"></div>
<section class="band hero">
  <div class="photo" role="img" aria-label="Smiling businesswoman in a dark blazer against city towers"></div>
</section>
<div class="abs hero-mark"></div>
<h1 class="abs hero-title">WE ARE BRIGHT SPARROW</h1>
<p class="abs hero-sub">AND I WILL CONQUER THE WORLD</p>
<form class="abs signup hero-form"><div class="field">SPARROW@Email.com</div><div class="go">LET'S FLY</div></form>

<!-- intro -->
<div class="abs badge-square intro-mark"></div>
<h2 class="abs intro-title">WE ARE BRIGHT SPARROW IS A GLOBAL EMPOWERMENT</h2>
<p class="abs intro-sub">MOVEMENT ELEVATING WOMEN... AND THE WORLD.</p>
<a class="abs fly-box" href="#"><span class="sq"></span><span><small>LET'S</small><b>FLY</b></span></a>

<!-- who we are -->
<section class="band who" id="mission">
  <div class="photo" role="img" aria-label="Smiling woman with long brown hair in an office"></div>
</section>
<a class="abs title-lockup on-dark" href="#mission" style="left:114px;top:1150px"><span class="lockup-square"></span><span class="lockup-text" style="font-size:32px"><span>WHO</span><span>WE</span><b>ARE</b></span></a>
<div class="abs divider" style="left:322px;top:1150px;height:95px"></div>
<p class="abs copy light" style="left:354px;top:1150px;width:756px">Sed ut perspiciatis unde omnis iste natus error sit voluptatem accusantium doloremque laudantium, totam rem aperiam, eaque ipsa quae ab illo inventore veritatis et quasi architecto beatae vitae dicta sunt explicabo aspernatur aut odit aut fugit, sed quia consequuntur magni dolores eos qui ratione voluptatem sequi nesciunt.</p>

<!-- mantra -->
<section class="band mantra" id="mantra">
  <div class="photo" role="img" aria-label="Faint teal-tinted portrait of a smiling woman"></div>
</section>
<p class="abs copy light" style="left:97px;top:1460px;width:650px">Sed ut perspiciatis unde omnis iste natus error sit voluptatem accusantium doloremque laudantium, totam rem aperiam, eaque ipsa quae ab illo inventore veritatis et quasi architecto beatae vitae dicta sunt explicabo aspernatur aut odit aut fugit, sed quia clone m sequi nesciunt.</p>
<div class="abs divider" style="left:771px;top:1468px;height:80px;background:rgba(0,0,0,.15)"></div>
<a class="abs title-lockup on-light" href="#mantra" style="left:800px;top:1468px"><span class="lockup-square"></span><span class="lockup-text" style="font-size:44px"><b>OUR</b><span>MANTRA</span></span></a>

<!-- meet -->
<section class="band meet" id="meet">
  <div class="photo" role="img" aria-label="Silhouette of a woman raising her arms at sunset"></div>
</section>
<section class="band armor" id="shirt"></section>
<div class="band mantra" style="clip-path:polygon(0 280px,100% 280px,100% 325px,50% 410px,0 325px)"></div>
<a class="abs title-lockup on-dark" href="#meet" style="left:97px;top:1794px"><span class="lockup-square"></span><span class="lockup-text" style="font-size:28px"><b>MEET</b><span>BRIGHT</span><b>SPARROWS</b></span></a>
<div class="abs divider" style="left:345px;top:1794px;height:85px"></div>
<p class="abs copy light" style="left:368px;top:1790px;width:740px">Sed ut perspiciatis unde omnis iste natus error sit voluptatem accusantium doloremque laudantium, totam rem aperiam, eaque ipsa quae ab illo inventore veritatis et quasi architecto beatae vitae dicta sunt explicabo aspernatur aut odit aut fugit, sed quia consequuntur magni dolores eos qui ratione voluptatem sequi nesciunt.</p>

<!-- show off background -->
<section class="band show" style="z-index:0">
  <div class="photo" role="img" aria-label="Smiling blonde woman in a bright room"></div>
</section>
<section class="band armor" style="z-index:1;clip-path:polygon(0 350px,100% 350px,100% 410px,50% 495px,0 410px)"></section>

<!-- armor content -->
<div class="abs product-photo content" role="img" aria-label="Product photo of the blue brand T-shirt"></div>
<h3 class="abs product-name content">QUIS NOSTRUD EXERCIT</h3>
<p class="abs product-desc content">Sed do eiusmod tempor incididunt ut labore et dolore magna aliquam ad minim veniamquis nostrud ex</p>
<div class="abs price content">$66.83</div>
<div class="abs stars content">★★★★★</div>
<div class="abs spec content" style="top:2230px">Size : M</div>
<div class="abs spec content" style="top:2254px">Color : Blue</div>
<a class="abs cart content" href="#">ADD TO CART</a>
<div class="abs divider dark content" style="left:807px;top:2180px;height:70px"></div>
<a class="abs title-lockup on-light content" href="#shirt" style="left:841px;top:2170px"><span class="lockup-square"></span><span class="lockup-text" style="font-size:44px"><b>OUR</b><span>ARMOR</span></span></a>

<!-- show off content -->
<div class="abs title-lockup on-dark" style="left:286px;top:2525px;z-index:2"><span class="lockup-square" style="width:50px;height:50px;border-width:6px"></span><span class="lockup-text"><b style="font-size:13px">SHOW OFF YOUR</b><span style="font-size:26px">SUPER</span><b style="font-size:26px">POWERS</b></span></div>
<div class="abs divider" style="left:545px;top:2522px;height:84px;z-index:2"></div>
<a class="abs social-big" href="#" style="left:580px;top:2552px;z-index:2"><i></i>PAGEWAVE</a>
<a class="abs social-big" href="#" style="left:760px;top:2552px;z-index:2"><i></i>PICTOLANE</a>

<!-- featured -->
<section class="band featured" style="z-index:3"></section>
<div class="abs member" style="left:177px;top:2783px;z-index:4"><div class="member-photo" role="img" aria-label="Portrait of a smiling woman in sunglasses" style="background:linear-gradient(135deg,#7a6a5c,#d8b9a0)"></div></div>
<div class="abs member" style="left:461px;top:2783px;z-index:4"><div class="member-photo" role="img" aria-label="Portrait of a smiling woman with dark hair" style="background:linear-gradient(135deg,#e8e4df,#b78c70)"></div></div>
<div class="abs member-name" style="left:124px;top:2996px;z-index:4">EOS QUIRATIONE</div>
<div class="abs member-role" style="left:124px;top:3022px;z-index:4">Nemo enim ipsam voluptvoluptas</div>
<div class="abs member-name" style="left:408px;top:2996px;z-index:4">EQUIRATIONE</div>
<div class="abs member-role" style="left:408px;top:3022px;z-index:4">Nemo enim ipsam voluptvoluptas</div>
<div class="abs divider" style="left:759px;top:2862px;height:96px;z-index:4;background:rgba(0,0,0,.15)"></div>
<div class="abs title-lockup on-light" style="left:788px;top:2860px;z-index:4"><span class="lockup-square"></span><span class="lockup-text" style="font-size:32px"><b>FEATURED</b><span>BRIGHT</span><b>SPARROW</b></span></div>

<!-- join -->
<div class="abs badge-square join-mark"></div>
<h2 class="abs join-title">JOIN US</h2>
<p class="abs join-copy">Sed ut perspiciatis unde omnis iste natus error sit voluptatem accusantium<br>doloremquist voluptatatus errorptatm aperaque.</p>
<form class="abs signup join-form"><div class="field">SPARROW@Email.com</div><div class="go">LET'S FLY</div></form>
<div class="abs foot-social">
  <a class="social-link" href="#"><span class="social-dot"></span>PAGEWAVE</a>
  <a class="social-link" href="#"><span class="social-dot alt"></span>PICTOLANE</a>
</div>
<nav class="abs foot-nav">
  <a href="#mission" style="left:0;top:0">MISSION</a>
  <a href="#mantra" style="left:115px;top:0">MANTRA</a>
  <a href="#meet" style="left:228px;top:0">MEET BS <span class="nav-square"></span></a>
  <a href="#shirt" style="left:340px;top:0">THE SHIRT</a>
</nav>
<p class="abs copyright">Copyright © 2017 Bright Sparrow. All rights reserved.</p>

</body>
</html>
```